Business Card Design for company

We want new business cards. We'd like something different-- yet still highly professional. Our tagline is Providing leadership, delivering success. Stock photos are ok, as long as they are relevant and look upscale.

Target Market(s)

Architecture/Business Management Consulting/Engineering Consulting

Contact Information for Business Card

dark gray background with pops of blue might be good, but you tell me. You're the designers. Rounded corners might be nice, but again, you tell me.

Font styles to use
Serif
Sans Serif

Colors
3276b5
5c5c5c
9d9d9d
fbfbfb

Requirements
Nice to have
• Something different, but still very professional.

```html
<!DOCTYPE html>
<html lang="en">
<head>
<meta charset="utf-8">
<title>Arvenza Partners – Business Card</title>
<link rel="stylesheet" href="https://fonts.googleapis.com/css2?family=Work+Sans:wght@400;500;600&display=swap">
<style>
  :root {
    --page: #161616;
    --card: #2e2e2f;
    --card-back: #262627;
    --blue: #3276b5;
    --grey: #5c5c5c;
    --light-grey: #9d9d9d;
    --white: #fbfbfb;
  }
  html, body {
    margin: 0;
    padding: 0;
    overflow: hidden;
    background: var(--page);
  }
  .canvas {
    position: relative;
    width: 1200px;
    height: 900px;
    background: var(--page);
    font-family: "Work Sans", sans-serif;
    overflow: hidden;
  }
  .card {
    position: absolute;
    left: 250px;
    width: 700px;
    height: 400px;
    box-sizing: border-box;
  }
  .card-back {
    top: 40px;
    background: var(--card-back);
    display: flex;
    align-items: center;
    justify-content: center;
  }
  .card-back .brand-name {
    color: var(--white);
    font-size: 34px;
    font-weight: 600;
    letter-spacing: 4px;
    text-transform: uppercase;
  }
  .card-front {
    top: 460px;
    background: var(--card);
    display: flex;
    align-items: center;
    padding: 0 40px 0 44px;
  }
  .brand-block {
    width: 300px;
  }
  .brand-block .brand-name {
    color: var(--blue);
    font-weight: 600;
    text-transform: uppercase;
    line-height: 1;
    margin: 0;
  }
  .brand-name .primary {
    display: block;
    font-size: 58px;
    letter-spacing: 1px;
  }
  .brand-name .secondary {
    display: block;
    font-size: 26px;
    letter-spacing: 6px;
    margin-top: 10px;
  }
  .divider {
    width: 2px;
    height: 190px;
    background: var(--white);
    margin: 0 34px 0 18px;
  }
  .contact-block {
    color: var(--white);
    font-size: 17px;
    line-height: 1.35;
  }
  .person-name {
    color: var(--blue);
    font-size: 25px;
    font-weight: 500;
    letter-spacing: 2px;
    text-transform: uppercase;
    margin: 0;
  }
  .person-role {
    font-size: 17px;
    margin: 0 0 16px;
  }
  .address {
    margin: 0 0 12px;
    letter-spacing: 0.5px;
  }
  .contact-line {
    display: flex;
    align-items: center;
    gap: 10px;
    margin: 2px 0;
    letter-spacing: 0.5px;
  }
  .contact-line svg {
    width: 12px;
    height: 12px;
    flex: none;
  }
</style>
</head>
<body>
<div class="canvas">
  <section class="card card-back">
    <span class="brand-name">Arvenza</span>
  </section>

  <section class="card card-front">
    <div class="brand-block">
      <p class="brand-name">
        <span class="primary">Arvenza</span>
        <span class="secondary">Partners</span>
      </p>
    </div>
    <div class="divider"></div>
    <div class="contact-block">
      <h1 class="person-name">Daniel Reyes</h1>
      <p class="person-role">Director</p>
      <p class="address">58 Harlow Lane,<br>Wellington, NZ, 6011</p>
      <p class="contact-line">
        <svg viewBox="0 0 12 12" aria-hidden="true"><path d="M2.5 1 L4.5 1 L5 3.5 L3.8 4.3 Q4.8 6.8 7.7 8.2 L8.5 7 L11 7.5 L11 9.5 Q10.5 11 9 11 Q1 10 1 2.5 Q1 1.2 2.5 1 Z" fill="var(--blue)"/></svg>
        (555) 014-2290
      </p>
      <p class="contact-line">
        <svg viewBox="0 0 12 12" aria-hidden="true"><rect x="0.8" y="2.5" width="10.4" height="7" fill="none" stroke="var(--blue)" stroke-width="1.2"/><path d="M1 3 L6 6.8 L11 3" fill="none" stroke="var(--blue)" stroke-width="1.2"/></svg>
        hello@arvenzapartners.com
      </p>
      <p class="contact-line">
        <svg viewBox="0 0 12 12" aria-hidden="true"><circle cx="6" cy="6" r="5" fill="none" stroke="var(--blue)" stroke-width="1.1"/><ellipse cx="6" cy="6" rx="2.2" ry="5" fill="none" stroke="var(--blue)" stroke-width="1"/><path d="M1 6 H11" stroke="var(--blue)" stroke-width="1"/></svg>
        www.arvenzapartners.com
      </p>
    </div>
  </section>
</div>
</body>
</html>
```